KDWB Business Card

Looking for a business card design to incorporate our branding. We want to only use the colors listing in the Branding Package (attached).
Updates

Target Market(s)

People who need their phone or device fixed.

Industry/Entity Type

Electronics

Contact Information for Business Card

Please use:

Brightwick Gadget Clinic LLC
4810 E Harlow Ridge Rd
Suite 417
San Antonio, TX 78163

Marcus Delgrove, Store Manager

(210) 555-0147

Requirements
Must have
• Must include the colors that are contained within the Branding Package PDF file.

```html
<!DOCTYPE html>
<html lang="en">
<head>
<meta charset="utf-8">
<title>Brightwick Gadget Clinic – Business Card</title>
<link rel="stylesheet" href="https://fonts.googleapis.com/css2?family=Quicksand:wght@400;500&family=Open+Sans:wght@400;600&display=swap">
<style>
  :root {
    --bg: #2e2927;
    --card-black: #1a1a1a;
    --card-white: #ffffff;
    --brand-orange: #f05a28;
    --text-light: #f2f2f2;
    --text-dark: #1a1a1a;
    --icon-bg: #ffffff;
  }
  * { box-sizing: border-box; margin: 0; padding: 0; }
  html, body {
    width: 1200px; height: 810px; overflow: hidden;
    background: var(--bg);
    font-family: "Open Sans", Arial, sans-serif;
  }
  .stage {
    position: relative; width: 1200px; height: 810px;
    display: flex; align-items: center; justify-content: center; gap: 60px;
  }
  .card {
    position: relative; width: 520px; height: 300px;
    border-radius: 14px; overflow: hidden;
    box-shadow: 0 10px 30px rgba(0,0,0,.45);
  }
  .card--back { background: var(--card-black); }
  .card--front { background: var(--card-white); }

  .brand {
    display: flex; align-items: center; gap: 12px;
    font-family: "Quicksand", Arial, sans-serif; font-weight: 500;
    color: var(--brand-orange);
  }
  .brand__square {
    background: var(--brand-orange); border: 3px solid var(--card-white);
    border-radius: 8px;
  }
  .card--back .brand {
    position: absolute; left: 50%; top: 50%; transform: translate(-50%, -50%);
    font-size: 30px; white-space: nowrap;
  }
  .card--back .brand__square { width: 54px; height: 54px; }

  .card--front .brand {
    position: absolute; left: 30px; top: 30px; font-size: 22px; white-space: nowrap;
  }
  .card--front .brand__square { width: 40px; height: 40px; border-color: #fbe0d6; }

  .wave { position: absolute; inset: 0; width: 100%; height: 100%; }

  .person {
    position: absolute; right: 30px; top: 130px; text-align: right;
  }
  .person__name { font-size: 21px; color: var(--text-dark); font-weight: 400; }
  .person__role { font-size: 12px; color: var(--brand-orange); margin-top: -2px; }

  .contacts {
    position: absolute; right: 24px; top: 205px;
    display: flex; flex-direction: column; gap: 6px; align-items: flex-end;
  }
  .contact {
    display: flex; align-items: center; gap: 10px;
    color: var(--text-light); font-size: 12px;
  }
  .contact__icon {
    width: 14px; height: 14px; background: var(--icon-bg); border-radius: 2px;
    display: block;
  }
  .address {
    position: absolute; left: 24px; right: 24px; bottom: 16px;
    display: flex; justify-content: space-between; align-items: center;
    color: var(--text-light); font-size: 12px;
  }
</style>
</head>
<body>
<main class="stage">
  <section class="card card--back" aria-label="Card back">
    <div class="brand">
      <span class="brand__square"></span>
      <span class="brand__name">Brightwick Gadget Clinic</span>
    </div>
  </section>

  <section class="card card--front" aria-label="Card front">
    <svg class="wave" viewBox="0 0 520 300" preserveAspectRatio="none" aria-hidden="true">
      <path d="M0,108 C110,98 200,168 300,178 C400,188 470,184 520,200 L520,300 L0,300Z" fill="var(--brand-orange)"/>
      <path d="M0,122 C110,112 200,182 300,192 C400,202 470,200 520,216 L520,300 L0,300Z" fill="var(--card-black)"/>
    </svg>

    <div class="brand">
      <span class="brand__square"></span>
      <span class="brand__name">Brightwick Gadget Clinic</span>
    </div>

    <div class="person">
      <p class="person__name">Marcus Delgrove</p>
      <p class="person__role">Store Manager</p>
    </div>

    <div class="contacts">
      <p class="contact">(210) 555-0147
        <svg class="contact__icon" viewBox="0 0 14 14" aria-hidden="true"><rect width="14" height="14" rx="2" fill="#fff"/><path d="M4 3.5 L5.8 3.5 L6.3 5.6 L5.3 6.3 Q6.3 8.2 7.7 8.7 L8.4 7.7 L10.5 8.2 L10.5 10 Q6 10.5 4 3.5Z" fill="#1a1a1a"/></svg>
      </p>
      <p class="contact">marcus@brightwickclinic.com
        <svg class="contact__icon" viewBox="0 0 14 14" aria-hidden="true"><rect width="14" height="14" rx="2" fill="#fff"/><rect x="3" y="4.5" width="8" height="5.5" fill="none" stroke="#1a1a1a" stroke-width="1"/><path d="M3 4.5 L7 7.5 L11 4.5" fill="none" stroke="#1a1a1a" stroke-width="1"/></svg>
      </p>
      <p class="contact">www.brightwickclinic.com
        <svg class="contact__icon" viewBox="0 0 14 14" aria-hidden="true"><rect width="14" height="14" rx="2" fill="#fff"/><circle cx="7" cy="7" r="3.8" fill="none" stroke="#1a1a1a" stroke-width="1"/><path d="M3.2 7 H10.8 M7 3.2 Q5 7 7 10.8 M7 3.2 Q9 7 7 10.8" fill="none" stroke="#1a1a1a" stroke-width=".8"/></svg>
      </p>
    </div>

    <div class="address">
      <span>4810 E Harlow Ridge Rd, Suite 417, San Antonio, TX 78163</span>
      <svg class="contact__icon" viewBox="0 0 14 14" aria-hidden="true"><rect width="14" height="14" rx="2" fill="#fff"/><path d="M7 11.5 L4.4 7.2 A3 3 0 1 1 9.6 7.2Z" fill="#1a1a1a"/><circle cx="7" cy="5.6" r="1.1" fill="#fff"/></svg>
    </div>
  </section>
</main>
</body>
</html>
```